Flyer Design - Spill Management Products - Selling to new clients

I am looking to produce an A4 double sided flyer. It is promoting our spill management products to prospective clients. This flyer is specifically targetting coal mines near where we operate.
I am not sure if I have provided too much text to fit in 2 pages, if so, I can reduce it if needed.
As it is selling to prospective clients, I think it needs to grab their attention. I basically want a bit of text, selling us and our company too them, and then feature a number of products.
If you need more clarification on what we want, please ask.
I would like it designed in InDesign if possible, as we have someone in house that could make changes to it when needed. I also intend to have this professionally printed.
You can view our company here – www.tarnvale.com.au
I have added a word document with details of what is to be included, plus the required images.
Cheers,
Milo

```html
<!DOCTYPE html>
<html lang="en">
<head>
<meta charset="utf-8">
<title>Tarnvale – Spill Management Products</title>
<link href="https://fonts.googleapis.com/css2?family=Questrial&display=swap" rel="stylesheet">
<style>
  :root {
    --bg-light: #c4c5c7;
    --bg-mid: #9d9ea1;
    --bg-dark: #8a8b8e;
    --band-light: #f2f2f2;
    --band-dark: #a9aaad;
    --ink: #161616;
    --heading-red: #d4202a;
    --gold: #d8b62c;
    --gold-dark: #a88a16;
    --ribbon: #ffffff;
    --label-bg: #0c0c0c;
    --label-ink: #f3c21c;
    --swoosh: rgba(255,255,255,0.22);
  }
  * { margin: 0; padding: 0; box-sizing: border-box; }
  html, body { width: 860px; height: 1200px; overflow: hidden; background: #fff; }
  .flyer {
    position: relative;
    width: 860px; height: 1200px; overflow: hidden;
    background: radial-gradient(ellipse at 60% 45%, var(--bg-light) 0%, var(--bg-mid) 55%, var(--bg-dark) 100%);
    font-family: "Questrial", "Century Gothic", sans-serif;
    color: var(--ink);
  }
  .band { position: absolute; left: 0; width: 860px; background: linear-gradient(180deg, var(--band-light), var(--band-dark)); }
  .band--top { top: 0; height: 34px; }
  .band--bottom { bottom: 0; height: 34px; background: linear-gradient(0deg, var(--band-light), var(--band-dark)); }
  .swoosh { position: absolute; inset: 0; }
  .ribbons { position: absolute; top: 0; left: 0; }
  .content {
    position: absolute; left: 52px; top: 322px; width: 768px;
    font-size: 14.6px; line-height: 19px;
  }
  .section-title { color: var(--heading-red); font-style: italic; font-weight: 700; font-size: 15px; }
  .section { margin-bottom: 19px; }
  .feature { padding-left: 46px; }
  .feature::before { content: "▫ "; }
  .product { padding-left: 66px; }
  .product--deep { padding-left: 110px; }
  .other-label {
    position: absolute; left: 0; top: 885px; width: 160px; height: 30px;
    background: var(--label-bg); color: var(--label-ink);
    font-weight: 700; font-size: 16px; line-height: 30px; padding-left: 103px;
  }
  .other {
    position: absolute; left: 52px; top: 922px; width: 768px;
    font-size: 14.6px; line-height: 19px;
  }
  .contact {
    position: absolute; left: 0; top: 1032px; width: 860px; text-align: center;
    font-style: italic; font-weight: 700; font-size: 14.6px; line-height: 18.5px;
  }
</style>
</head>
<body>
<div class="flyer">
  <svg class="swoosh" width="860" height="1200" viewBox="0 0 860 1200" aria-hidden="true">
    <path d="M560 34 C420 300 720 520 560 800 C470 960 520 1080 640 1166 L700 1166 C590 1070 560 960 640 800 C790 520 500 300 620 34 Z" fill="var(--swoosh)"/>
  </svg>
  <div class="band band--top"></div>
  <div class="band band--bottom"></div>

  <svg class="ribbons" width="860" height="330" viewBox="0 0 860 330">
    <!-- left ribbon -->
    <path d="M62 92 Q62 86 80 86 L90 86 L90 104 Z" fill="var(--gold)"/>
    <path d="M70 100 L319 100 L319 302 L194 262 L70 302 Z" fill="var(--ribbon)"/>
    <rect x="96" y="112" width="196" height="138" fill="#e6e6e2" role="img" aria-label="Coiled white absorbent booms"/>
    <!-- middle ribbon -->
    <path d="M337 22 L504 22 L504 26 L337 26 Z" fill="var(--gold)"/>
    <path d="M333 22 L516 22 L516 314 L424 276 L333 314 Z" fill="var(--ribbon)"/>
    <rect x="376" y="36" width="96" height="236" fill="#8e8f91" role="img" aria-label="Roll of grey needle punch absorbent"/>
    <!-- right ribbon -->
    <path d="M788 92 Q796 86 778 86 L768 86 L768 104 Z" fill="var(--gold)"/>
    <path d="M540 100 L790 100 L790 302 L665 262 L540 302 Z" fill="var(--ribbon)"/>
    <rect x="552" y="112" width="168" height="142" fill="#c9b7a8" role="img" aria-label="Spill kit with red wheelie bin, pads, gloves and socks"/>
  </svg>

  <div class="content">
    <div class="section">
      <div class="section-title">Absorbents</div>
      <p>• We understand that absorbents are often for everyday use in mine workshops. We suplpy many mines a tough Needle Punch absorbent, to ensure if can handle foot and machinery traffic. We also supply a recycled absorbent in oil only and unvisersal types, as a natural laternative to polypropylene absoprbents.</p>
      <p class="feature">Feature the below products</p>
      <p class="product">• Universal Grey Needle Punch Absorbent Roll – Heavy Weight (96cm x 43m) (image name -</p>
      <p>• A heavy weight grey universal needle punch absorbent roll designed to withstand forklift and foot traffic. It can cover long areas quickly. Absorbs water-based liquids and oil-based fluids.</p>
      <p>• Rolls are perforated on the centre 48 cm and across every 43 cm. So can be torn into pads</p>
    </div>
    <div class="section">
      <div class="section-title">Floor Sweeps</div>
      <p>• Some mines have a prefernce for using floor sweeps over absorbent pads, so we ensure we always stock a range of floow sweeps, capable of hanlding any spill. We supply floor sweeps suitable for indoor or ourdoor, and oil or chemical spills.</p>
      <p class="feature">Feature the below product</p>
      <p class="product">• Organic Floor Sweep (Image name -</p>
      <p><span style="padding-left:110px">• Our Organic Absorbent Floor Sweep is manufactured locally from recycled organic</span> cellulose products that would otherwise end up in landfills. It encapsulates liquids and stops them from leaching out of the absorbent.. Naturally occurring microbes contained in the cellulose material consume hydrocarbons like fuel, oil and grease and gradually convert them into a composted material.</p>
    </div>
    <div class="section">
      <div class="section-title">Absorbent Booms</div>
      <p>• We know that oil spills on water can sometime be an issue in the mining industry. We supply many mines with polyproylene floating boom.</p>
      <p>• The all-in-one construction stitches the sock and net together and aligns the rope along one side. The boom also has rust proof end rings and snaps hooks, so you can link booms together to make an effective barrier.</p>
      <p class="feature">Feature the below product</p>
      <p class="product" style="padding-left:76px">• OIL AND PETROLEUM WHITE COTTON/POLYPROPYLENE MIX BOOM (3M X 12.5CM)</p>
    </div>
  </div>

  <div class="other-label">Other:</div>
  <div class="other">
    <p>• We supply any Spill Management product that you would need. Check out our website for our full range at www.tarnvale.com.au</p>
    <p>• Call us today to organise a product demonstration, or an obligation free quote.</p>
  </div>

  <div class="contact">
    <p>Our contact Details:</p>
    <p>Tarnvale (A product of Kestrel Safety Services)</p>
    <p>Phone Number: 1300 555 019</p>
    <p>Facsimile Number: (02) 4955 0123</p>
    <p>Trading Address: 1st Floor, 42 Harbour St Wickham NSW 2293</p>
    <p>Mailing Address: PO Box 207 Wickham NSW 2293</p>
    <p>Web :www.tarnvale.au</p>
  </div>
</div>
</body>
</html>
```